Corporate Business Card

Very professional, Modern, Not to busy, include phone address email, website
(253) 617-4930, 18761 52nd Avenue S, Kent, WA 98047, martin@plumlinegroup.com, varkoworks.com

Target Market(s)

Manufacturing

Industry/Entity Type

Aero, machining, manufacturing, Off road racing

Contact Information for Business Card

Phone, address email, website

```html
<!DOCTYPE html>
<html lang="en">
<head>
<meta charset="utf-8">
<title>Varko Works – Business Card</title>
<link href="https://fonts.googleapis.com/css2?family=Barlow:wght@500;700&display=swap" rel="stylesheet">
<style>
  :root {
    --navy: #2f4473;
    --ink: #111111;
    --icon: #333333;
    --paper: #ffffff;
    --wash: #eceef3;
  }
  html, body {
    margin: 0;
    padding: 0;
    width: 1200px;
    height: 682px;
    overflow: hidden;
    background: var(--paper);
  }
  .card {
    position: relative;
    width: 1200px;
    height: 682px;
    background: var(--paper);
    font-family: "Barlow", sans-serif;
  }
  .brand-name {
    position: absolute;
    left: 121px;
    top: 128px;
    margin: 0;
    font-family: "Barlow", sans-serif;
    font-weight: 700;
    font-size: 78px;
    line-height: 1;
    letter-spacing: 1px;
    color: var(--navy);
  }
  .backdrop-band {
    position: absolute;
    left: 0;
    top: 351px;
    width: 616px;
    height: 289px;
    background: var(--wash);
  }
  .contact-list {
    position: absolute;
    left: 594px;
    top: 400px;
    margin: 0;
    padding: 0;
    list-style: none;
    color: var(--ink);
    font-size: 37px;
    font-weight: 500;
    line-height: 42.5px;
    letter-spacing: 0.6px;
  }
  .contact-item {
    display: flex;
    align-items: flex-start;
  }
  .contact-icon {
    flex: 0 0 26px;
    width: 26px;
    height: 26px;
    margin-top: 8px;
    margin-right: 28px;
    fill: var(--icon);
  }
  .contact-text {
    white-space: nowrap;
  }
</style>
</head>
<body>
  <div class="card">
    <h1 class="brand-name">Varko Works</h1>

    <div class="backdrop-band" aria-hidden="true"></div>

    <ul class="contact-list">
      <li class="contact-item">
        <svg class="contact-icon" viewBox="0 0 24 24" aria-hidden="true">
          <rect x="5" y="1" width="14" height="22" rx="2"/>
          <circle cx="12" cy="3.2" r="0.7" fill="#fff"/>
          <circle cx="12" cy="20.5" r="0.8" fill="#fff"/>
        </svg>
        <span class="contact-text">(253) 617-4930,</span>
      </li>
      <li class="contact-item">
        <svg class="contact-icon" viewBox="0 0 24 24" aria-hidden="true">
          <path d="M12 1a8 8 0 0 0-8 8c0 6 8 14 8 14s8-8 8-14a8 8 0 0 0-8-8zm0 11a3.2 3.2 0 1 1 0-6.4 3.2 3.2 0 0 1 0 6.4z"/>
        </svg>
        <span class="contact-text">18761 52nd Avenue S,<br>Kent, WA 98047,</span>
      </li>
      <li class="contact-item">
        <svg class="contact-icon" viewBox="0 0 24 24" aria-hidden="true">
          <path d="M2 4h20a1 1 0 0 1 1 1v14a1 1 0 0 1-1 1H2a1 1 0 0 1-1-1V5a1 1 0 0 1 1-1zm1.5 2.2L12 13l8.5-6.8V6h-17z"/>
        </svg>
        <span class="contact-text">martin@plumlinegroup.com</span>
      </li>
      <li class="contact-item">
        <svg class="contact-icon" viewBox="0 0 24 24" aria-hidden="true">
          <path d="M12 1a11 11 0 1 0 0 22 11 11 0 0 0 0-22zm-1.2 2.3v7.7H6.5c.2-3.4 1.9-6.3 4.3-7.7zm2.4 0c2.4 1.4 4.1 4.3 4.3 7.7h-4.3zM3.1 11h1.9c.1-2.6 1-5 2.4-6.8A9 9 0 0 0 3.1 11zm13.5-6.8c1.4 1.8 2.3 4.2 2.4 6.8h1.9a9 9 0 0 0-4.3-6.8zM3.1 13a9 9 0 0 0 4.3 6.8C6 18 5.1 15.6 5 13zm3.4 0h4.3v7.7C8.4 19.3 6.7 16.4 6.5 13zm6.7 0h4.3c-.2 3.4-1.9 6.3-4.3 7.7zm5.8 0c-.1 2.6-1 5-2.4 6.8a9 9 0 0 0 4.3-6.8z"/>
        </svg>
        <span class="contact-text">varkoworks.com</span>
      </li>
    </ul>
  </div>
</body>
</html>
```